Wordpress template for a mens-choire webpage

Task is to design a Wordpress template for an 98 years old estonian mens choire webpage.
Design should involve details from the attached files, choire logo and the colors of the choire flag: in horizontal orientation bright sky-blue, white, bright grass-green.
Designer signature is allowed to be added to the template, with country of origin.

Reason: Deadline extended 2 days (until 2. March 2014) to accommodate designers creativity.

Thank you everyone for your great designs!
Our project has now entered into a voting and decision phase until 14th of March 2014 (included).

```html
<!DOCTYPE html>
<html lang="en">
<head>
<meta charset="utf-8">
<title>Kaiku Singers</title>
<link href="https://fonts.googleapis.com/css2?family=Open+Sans:ital,wght@0,400;0,600;1,400&family=Ubuntu:wght@500&family=Oswald:wght@400&display=swap" rel="stylesheet">
<style>
:root{
  --red:#b30b0b;
  --red-text:#c20e0e;
  --gold:#cf9830;
  --gold-text:#b8862a;
  --sky:#4d8be0;
  --sky-light:#bcd7f3;
  --grass:#7be04a;
  --text:#666;
  --dark:#333;
  --card:#f7f7f7;
  --line:#dedede;
  --footer:#4a4a4a;
  --footer-text:#bdbdbd;
}
*{margin:0;padding:0;box-sizing:border-box}
html,body{width:1108px;height:1200px;overflow:hidden;background:#fff}
body{position:relative;font-family:"Open Sans",Arial,sans-serif;color:var(--text)}
.abs{position:absolute}
h1,h2,h3{font-weight:400}

.sky-backdrop{left:0;top:0;width:1108px;height:470px;
  background:
   radial-gradient(ellipse 140px 70px at 60px 120px,var(--grass),transparent 70%),
   radial-gradient(ellipse 140px 70px at 1050px 120px,var(--grass),transparent 70%),
   linear-gradient(180deg,#8fb8e8 0%,var(--sky-light) 25%,#e9f2fb 55%,var(--sky) 62%,#9fc0ec 75%,#fff 100%)}

.main-nav{left:120px;top:73px;width:868px;height:44px;background:var(--red);border-radius:3px 3px 0 0}
.main-nav a{position:absolute;top:14px;color:#fff;font-size:12px;font-weight:600;text-decoration:none;letter-spacing:.3px}

.brand-badge{left:496px;top:20px;width:116px;height:116px;border-radius:50%;background:#fff;border:4px solid var(--red);
  display:flex;align-items:center;justify-content:center;text-align:center}
.brand-badge span{color:var(--red);font-size:13px;font-weight:600;line-height:17px}

.slider{left:120px;top:117px;width:868px;height:328px;background:#fff;padding:5px;box-shadow:0 1px 3px rgba(0,0,0,.25)}
.slider-photo{width:100%;height:100%;background:linear-gradient(90deg,#8d7a60 0%,#a58e70 40%,#3a2a26 60%,#6a2020 80%,#8a7a62 100%)}
.slide-title{left:155px;top:183px;color:#fff;font-family:"Ubuntu",Arial,sans-serif;font-weight:500;text-shadow:1px 2px 3px rgba(0,0,0,.6);line-height:42px}
.slide-title .big{font-size:52px}
.slide-title .mid{font-size:30px}
.slide-title .line2{font-size:39px;display:block}
.round-arrow{width:26px;height:26px;border-radius:50%;display:flex;align-items:center;justify-content:center}
.round-arrow.grey{background:#9a9a9a}
.round-arrow.beige{background:#f3e3c2}

.welcome-title{left:0;width:1108px;top:468px;text-align:center;color:var(--red-text);font-size:22px}
.welcome-text{left:122px;width:864px;top:504px;text-align:center;font-size:12.2px;line-height:21.3px}

.gallery{left:120px;top:615px;width:868px;height:207px;background:var(--gold);border-radius:2px}
.gallery-label{position:absolute;left:370px;top:20px;width:129px;height:35px;background:#fff;color:var(--red-text);font-size:22px;text-align:center;line-height:35px}
.gallery-thumb{position:absolute;top:75px;width:186px;height:115px;background:#fff;padding:5px;box-shadow:0 1px 2px rgba(0,0,0,.2)}
.gallery-thumb div{width:100%;height:100%}

.divider{left:120px;width:868px;top:847px;height:1px;background:var(--line)}
.section-title{top:863px;color:var(--red-text);font-size:22px}
.updown{top:872px;width:28px;height:14px}

.news-card{left:120px;width:399px;height:80px;background:var(--card);border:1px solid var(--line)}
.news-date{position:absolute;left:12px;top:10px;width:36px;text-align:center;font-family:"Oswald",Arial,sans-serif}
.news-date .month{display:block;color:var(--gold-text);font-size:16px;line-height:20px}
.news-date .day{display:block;color:var(--red-text);font-size:36px;line-height:38px}
.news-body{position:absolute;left:54px;top:8px;width:340px;font-size:12.2px;line-height:21.3px}
.read-more{color:var(--red-text);font-style:italic;font-size:11px}

.event{left:572px;width:416px}
.event-photo{position:absolute;left:2px;top:0;width:82px;height:65px;background:linear-gradient(180deg,#2a1c1a,#5a2e28 60%,#9a6a3a)}
.event-title{position:absolute;left:99px;top:-4px;color:var(--dark);font-size:14.5px;letter-spacing:.3px}
.event-text{position:absolute;left:99px;top:18px;width:318px;font-size:12.2px;line-height:21.3px}
.event-rule{left:572px;width:416px;top:985px;height:1px;background:var(--line)}

.site-footer{left:0;top:1092px;width:1108px;height:108px;background:var(--footer)}
.copyright{position:absolute;left:120px;top:34px;color:var(--footer-text);font-size:11.5px;line-height:21px}
.copyright strong{color:#fff;font-weight:400}
.social{position:absolute;top:36px;width:37px;height:37px;border-radius:50%}
</style>
</head>
<body>

<div class="abs sky-backdrop" role="img" aria-label="Choir flags in sky-blue, white and grass-green waving against the sky"></div>

<nav class="abs main-nav">
  <a style="left:20px">HOME</a>
  <a style="left:95px">ABOUT US</a>
  <a style="left:197px">GALLERY</a>
  <a style="left:292px">SERVICES</a>
  <a style="left:524px">BLOG</a>
  <a style="left:604px">NEWS</a>
  <a style="left:683px">EVENTS</a>
  <a style="left:771px">CONTACT US</a>
</nav>

<div class="abs slider">
  <div class="slider-photo" role="img" aria-label="Choir members in traditional dress standing on stone steps before an old arch"></div>
</div>

<div class="abs brand-badge"><span>Kaiku<br>Singers</span></div>

<h1 class="abs slide-title"><span class="big">98</span> <span class="mid">Years of</span><span class="line2">Estonian Choire</span></h1>

<div class="abs round-arrow grey" style="left:155px;top:397px"><svg width="10" height="10" viewBox="0 0 10 10"><path d="M6.5 1.5 3 5l3.5 3.5" fill="none" stroke="#fff" stroke-width="2"/></svg></div>
<div class="abs round-arrow grey" style="left:186px;top:397px"><svg width="10" height="10" viewBox="0 0 10 10"><path d="M3.5 1.5 7 5 3.5 8.5" fill="none" stroke="#fff" stroke-width="2"/></svg></div>

<h2 class="abs welcome-title">Welcome to Our Website</h2>
<p class="abs welcome-text">Aliquam molestie, mi et imperdiet euismod, dui purus auctor tellus, et interdum lacus lectus et ante. Sed accumsan sollicitudin sapien, sit amet adipiscing turpis gravida ac. In congue, neque ac lobortis volutpat, libero mauris varius mi, vitae suscipit ipsum ligula vitae risus. Duis aliquam nibh a dui iaculis viverra id a velit. Vivamus egestas risus in magna varius commodo. Sed semper viverra egestas. Etiam pretium porttitor lectus, vel ornare neque porta volutpat.</p>

<section class="abs gallery">
  <div class="gallery-label">Gallery</div>
  <div class="abs round-arrow beige" style="left:5px;top:120px"><svg width="10" height="10" viewBox="0 0 10 10"><path d="M6.5 1.5 3 5l3.5 3.5" fill="none" stroke="var(--gold)" stroke-width="2"/></svg></div>
  <div class="gallery-thumb" style="left:36px"><div role="img" aria-label="Choir in black suits on a grey studio backdrop" style="background:linear-gradient(180deg,#c9ccd2,#8e9096 55%,#2a2a2e)"></div></div>
  <div class="gallery-thumb" style="left:239px"><div role="img" aria-label="Choir in traditional dress before a stone arch" style="background:linear-gradient(90deg,#9a8a70,#3a2a28 50%,#8a7a66)"></div></div>
  <div class="gallery-thumb" style="left:443px"><div role="img" aria-label="Large choir in dark suits on stage" style="background:linear-gradient(180deg,#2a2e40,#4a4e66 50%,#1a1c24)"></div></div>
  <div class="gallery-thumb" style="left:646px"><div role="img" aria-label="Choir members posing in casual white shirts" style="background:linear-gradient(180deg,#8ea08a,#5a6a58 50%,#2a3028)"></div></div>
  <div class="abs round-arrow beige" style="left:836px;top:120px"><svg width="10" height="10" viewBox="0 0 10 10"><path d="M3.5 1.5 7 5 3.5 8.5" fill="none" stroke="var(--gold)" stroke-width="2"/></svg></div>
</section>

<div class="abs divider"></div>

<h2 class="abs section-title" style="left:120px">News</h2>
<svg class="abs updown" style="left:490px" viewBox="0 0 28 14"><path d="M3 9l4-4 4 4M17 5l4 4 4-4" fill="none" stroke="#555" stroke-width="2"/></svg>

<article class="abs news-card" style="top:901px">
  <div class="news-date"><span class="month">Feb</span><span class="day">14</span></div>
  <p class="news-body">Aliquam molestie, mi et imperdiet euismod, dui purus tellus, et interdum lacus lectus et ante. Sed accumsan sollicitudin sapie.. <span class="read-more">Read More</span></p>
</article>
<article class="abs news-card" style="top:989px">
  <div class="news-date"><span class="month">Feb</span><span class="day">14</span></div>
  <p class="news-body">Aliquam molestie, mi et imperdiet euismod, dui purus tellus, et interdum lacus lectus et ante. Sed accumsan sollicitudin sapie.. <span class="read-more">Read More</span></p>
</article>

<h2 class="abs section-title" style="left:572px">Events</h2>
<svg class="abs updown" style="left:958px" viewBox="0 0 28 14"><path d="M3 9l4-4 4 4M17 5l4 4 4-4" fill="none" stroke="#555" stroke-width="2"/></svg>

<article class="abs event" style="top:902px">
  <div class="event-photo" role="img" aria-label="Choir performing on a lit stage"></div>
  <h3 class="event-title">Nam fermentum vestibulum purus</h3>
  <p class="event-text">Aliquam molestie, mi et imperdiet euismod, dui purus tellus, et interdum lacus lectus et ante....<span class="read-more">Read More</span></p>
</article>
<div class="abs event-rule"></div>
<article class="abs event" style="top:1000px">
  <div class="event-photo" role="img" aria-label="Choir rows in dark suits" style="background:linear-gradient(180deg,#3a2a22,#1a1616 50%,#5a3a2a)"></div>
  <h3 class="event-title">Nam fermentum vestibulum purus</h3>
  <p class="event-text">Aliquam molestie, mi et imperdiet euismod, dui purus tellus, et interdum lacus lectus et ante....<span class="read-more">Read More</span></p>
</article>

<footer class="abs site-footer">
  <p class="copyright">CopyRight ©2014. <strong>Company Name</strong><br>All Right Reserved</p>
  <span class="social" style="left:823px;background:#3b5a98" aria-label="Social link"></span>
  <span class="social" style="left:866px;background:#2aa5a0" aria-label="Social link"></span>
  <span class="social" style="left:909px;background:#cc3a2e" aria-label="Social link"></span>
  <span class="social" style="left:951px;background:#d4472c" aria-label="Social link"></span>
</footer>

</body>
</html>
```